Vantiqo custom business card design

Need a authentic, innovative business card design for a new mobile app business. I am uploading a few screen images from our app for you to view. I would like app design theme to match business card design. I can also send logo images.

```html
<!DOCTYPE html>
<html lang="en">
<head>
<meta charset="utf-8">
<title>Vantiqo Business Card</title>
<link href="https://fonts.googleapis.com/css2?family=Work+Sans:wght@400;500;700&display=swap" rel="stylesheet">
<style>
  :root {
    --page-bg: #d8d2cb;
    --card-clear: #ebe6e0;
    --card-edge: #cfc8c0;
    --purple-deep: #4e1a6c;
    --purple-mid: #6a2692;
    --purple-light: #8a4fae;
    --mark-dark: #232125;
    --ink-light: #ebe2d6;
  }
  html, body {
    margin: 0;
    width: 1200px;
    height: 1047px;
    overflow: hidden;
    background: var(--page-bg);
    font-family: "Work Sans", Arial, sans-serif;
  }
  .card {
    position: absolute;
    left: 100px;
    top: 252px;
    width: 1000px;
    height: 543px;
    border-radius: 22px;
    overflow: hidden;
    background: var(--card-clear);
    box-shadow: 0 0 0 1px var(--card-edge);
  }
  .card-art {
    position: absolute;
    inset: 0;
  }
  .card-info {
    position: absolute;
    left: 49px;
    top: 0;
    color: var(--ink-light);
  }
  .brand-name {
    position: absolute;
    top: 42px;
    left: 0;
    margin: 0;
    font-size: 64px;
    font-weight: 700;
    letter-spacing: 0.5px;
    white-space: nowrap;
  }
  .person-name {
    position: absolute;
    top: 172px;
    left: 0;
    margin: 0;
    font-size: 34px;
    font-weight: 500;
    white-space: nowrap;
  }
  .person-role {
    position: absolute;
    top: 220px;
    left: 0;
    margin: 0;
    font-size: 23px;
    font-weight: 400;
    letter-spacing: 0.5px;
  }
  .address {
    position: absolute;
    top: 270px;
    left: 0;
    margin: 0;
    font-size: 23px;
    line-height: 37px;
    font-style: normal;
    letter-spacing: 0.6px;
    white-space: nowrap;
  }
  .contact-list {
    position: absolute;
    top: 364px;
    left: 0;
    margin: 0;
    padding: 0;
    list-style: none;
    font-size: 23px;
    letter-spacing: 0.6px;
  }
  .contact-item {
    display: flex;
    align-items: center;
    height: 36px;
    white-space: nowrap;
  }
  .contact-icon {
    width: 18px;
    height: 18px;
    margin-right: 16px;
    flex: none;
  }
</style>
</head>
<body>
  <div class="card">
    <svg class="card-art" width="1000" height="543" viewBox="0 0 1000 543">
      <defs>
        <linearGradient id="purplePanel" x1="0" y1="0" x2="1" y2="1">
          <stop offset="0" stop-color="var(--purple-mid)"/>
          <stop offset="0.55" stop-color="var(--purple-deep)"/>
          <stop offset="1" stop-color="var(--purple-light)"/>
        </linearGradient>
      </defs>
      <rect class="purple-panel" x="0" y="0" width="650" height="543" fill="url(#purplePanel)"/>
      <circle class="brand-circle" cx="730" cy="272" r="232" fill="var(--mark-dark)"/>
    </svg>

    <div class="card-info">
      <p class="brand-name">Vantiqo</p>
      <h1 class="person-name">DANIEL REYES</h1>
      <p class="person-role">Director</p>
      <address class="address">1827 Harbor Lane<br>Coral Bay, FL 32907</address>
      <ul class="contact-list">
        <li class="contact-item">
          <svg class="contact-icon" viewBox="0 0 18 18" fill="none" stroke="currentColor" stroke-width="1.8"><rect x="5" y="2" width="8" height="14" rx="1.5"/><line x1="8" y1="13" x2="10" y2="13"/></svg>
          (555) 418-2267
        </li>
        <li class="contact-item">
          <svg class="contact-icon" viewBox="0 0 18 18" fill="currentColor"><path d="M4.5 2.5l2.6 0.4 1 3.2-1.7 1.3c0.8 1.7 2 2.9 3.7 3.7l1.3-1.7 3.2 1 0.4 2.6c-0.6 1.1-1.6 1.7-2.8 1.6C7.5 14.1 3.9 10.5 3.4 5.3 3.3 4.1 3.6 3.1 4.5 2.5z"/></svg>
          (555) 730-9154
        </li>
        <li class="contact-item">
          <svg class="contact-icon" viewBox="0 0 18 18" fill="none" stroke="currentColor" stroke-width="1.6"><rect x="2" y="4" width="14" height="10" rx="1"/><polyline points="2.5,4.5 9,9.5 15.5,4.5"/></svg>
          info@Vantiqo.com
        </li>
        <li class="contact-item">
          <svg class="contact-icon" viewBox="0 0 18 18" fill="none" stroke="currentColor" stroke-width="1.4"><circle cx="9" cy="9" r="7"/><ellipse cx="9" cy="9" rx="3" ry="7"/><line x1="2" y1="9" x2="16" y2="9"/></svg>
          www.Vantiqo.com
        </li>
      </ul>
    </div>
  </div>
</body>
</html>
```